Dynamic Business Card for Sports Supplements Company

Hi! I'm looking for an awesome business card to match my existing sports supplement company. I have uploaded my current company logo and screenshot of the front page of my website.

I would like to have something dynamic and interesting and utilize the colors in the website - the reds and purples

The business card should be double sided and focus on a unique eye-catching design on the back and include all the relevant company info.

Most importantly, it should say somewhere: "Sign up on our website for a coupon code."

Target Market(s)

Mostly for women gym goers but it shouldn't be too feminine. It should be in keeping with the website design. It should flow and clearly be connected to it

Industry/Entity Type

Business

Contact Information for Business Card

Lorraine K. Vestal
CEO
LVestal@Quorvanexco.com
www.quorvanexco.com
555.417.3820
P.O. Box 47315
Halvern, Oregon 00000

Sign up on our website for a coupon code

Font styles to use
Serif
Sans Serif
Other font styles liked:
• Novecento font family and "Quorvanex" is in AR Destine font

Requirements
Must have
• One side should be a bold Quorvanex logo design. Even just the symbol itself may be o.k. (see attached file)

```html
<!DOCTYPE html>
<html lang="en">
<head>
<meta charset="utf-8">
<title>Quorvanex Business Card</title>
<link rel="stylesheet" href="https://fonts.googleapis.com/css2?family=Open+Sans:wght@400;600;800&display=swap">
<style>
  :root {
    --backdrop: #3a3330;
    --card-white: #f7f7f7;
    --card-black: #070707;
    --ink: #1a1a1a;
    --ink-soft: #333333;
    --accent-red: #e3262e;
    --mark-grey: #e4e4e4;
    --paper-white: #ffffff;
  }
  * { margin: 0; padding: 0; box-sizing: border-box; }
  html, body {
    width: 1200px;
    height: 844px;
    overflow: hidden;
    background: var(--backdrop);
    font-family: "Open Sans", Arial, sans-serif;
  }
  .stage {
    position: relative;
    width: 1200px;
    height: 844px;
  }
  .card {
    position: absolute;
    top: 268px;
    width: 540px;
    height: 309px;
    border-radius: 3px;
    box-shadow: 0 12px 30px rgba(0,0,0,0.45);
    overflow: hidden;
  }
  /* Front side */
  .card-front {
    left: 45px;
    background: var(--card-white);
    color: var(--ink);
  }
  .front-brand {
    position: absolute;
    top: 44px;
    left: 218px;
    text-align: left;
  }
  .brand-name {
    font-weight: 800;
    font-size: 36px;
    letter-spacing: 1px;
    text-transform: uppercase;
    line-height: 1;
  }
  .front-brand .brand-name { color: var(--ink); }
  .brand-tagline {
    font-size: 11px;
    letter-spacing: 2.6px;
    text-transform: uppercase;
    margin-top: 4px;
  }
  .front-brand .brand-tagline { color: var(--ink-soft); }
  .front-decor {
    position: absolute;
    left: 365px;
    top: 118px;
    width: 130px;
    height: 130px;
    background: var(--mark-grey);
    box-shadow: 4px 6px 10px rgba(0,0,0,0.12);
  }
  .contact-block {
    position: absolute;
    left: 42px;
    top: 150px;
  }
  .person-name {
    color: var(--accent-red);
    font-size: 17px;
    text-transform: uppercase;
    letter-spacing: 0.3px;
  }
  .person-role {
    font-size: 13px;
    margin-bottom: 8px;
  }
  .contact-list { list-style: none; }
  .contact-list li {
    display: flex;
    align-items: center;
    gap: 6px;
    font-size: 13px;
    line-height: 19px;
  }
  .contact-icon { width: 10px; height: 10px; flex: none; }
  .postal-address {
    font-size: 13px;
    line-height: 18px;
    margin-top: 10px;
    font-style: normal;
  }
  /* Back side */
  .card-back {
    left: 615px;
    background: var(--card-black);
    color: var(--paper-white);
  }
  .back-brand {
    position: absolute;
    top: 92px;
    left: 0;
    width: 100%;
    display: flex;
    flex-direction: column;
    align-items: center;
  }
  .brand-row {
    display: flex;
    align-items: center;
    gap: 10px;
  }
  .brand-square {
    width: 26px;
    height: 26px;
    background: var(--accent-red);
  }
  .back-brand .brand-name { color: var(--paper-white); font-size: 32px; }
  .back-brand .brand-tagline { color: var(--paper-white); font-size: 10px; }
  .coupon-line {
    position: absolute;
    top: 208px;
    left: 0;
    width: 100%;
    text-align: center;
    font-size: 13px;
    letter-spacing: 0.6px;
    text-transform: uppercase;
  }
</style>
</head>
<body>
<main class="stage">
  <section class="card card-front" aria-label="Card front">
    <div class="front-brand">
      <div class="brand-name">Quorvanex</div>
      <div class="brand-tagline">Your Training Companion</div>
    </div>
    <div class="front-decor"></div>
    <div class="contact-block">
      <div class="person-name">Lorraine K. Vestal</div>
      <div class="person-role">CEO</div>
      <ul class="contact-list">
        <li>
          <svg class="contact-icon" viewBox="0 0 10 10" aria-hidden="true"><path d="M2 0.5 L3.8 2.6 L2.8 3.8 Q4 6.3 6.2 7.2 L7.4 6.2 L9.5 8 L8.3 9.5 Q3.5 9 0.5 1.7 Z" fill="var(--accent-red)"/></svg>
          555.417.3820
        </li>
        <li>
          <svg class="contact-icon" viewBox="0 0 10 10" aria-hidden="true"><rect x="0.5" y="2" width="9" height="6.5" fill="var(--accent-red)"/><path d="M0.8 2.3 L5 5.6 L9.2 2.3" fill="none" stroke="var(--paper-white)" stroke-width="0.9"/></svg>
          LVestal@Quorvanexco.com
        </li>
        <li>
          <svg class="contact-icon" viewBox="0 0 10 10" aria-hidden="true"><circle cx="5" cy="5" r="4.5" fill="var(--accent-red)"/><path d="M0.8 5 H9.2 M5 0.6 Q2.5 5 5 9.4 M5 0.6 Q7.5 5 5 9.4" fill="none" stroke="var(--paper-white)" stroke-width="0.7"/></svg>
          www.quorvanexco.com
        </li>
      </ul>
      <address class="postal-address">
        P.O. Box 47315<br>
        Halvern, Oregon 00000
      </address>
    </div>
  </section>

  <section class="card card-back" aria-label="Card back">
    <div class="back-brand">
      <div class="brand-row">
        <span class="brand-square"></span>
        <span class="brand-name">Quorvanex</span>
      </div>
      <div class="brand-tagline">Your Training Companion</div>
    </div>
    <p class="coupon-line">Sign up on our website for a coupon code</p>
  </section>
</main>
</body>
</html>
```